Voranta Imports Busisness cards and logo

Voranta imports is a brand new wholesale company located in Londonderry, New Hampshire dedicated to finding unique products from around the world.
Licensed to sell wine and spirits in the state and also authorized distributors of Pale Meadow Design, a manufacturer of girls and women shoes. Other products that we are currently trying to import are cheese and frozen food from Spain.
We would like a design that portraits our diversity of products and wholesale capabilities

```html
<!DOCTYPE html>
<html lang="en">
<head>
<meta charset="utf-8">
<title>Voranta Imports – Business Card</title>
<link href="https://fonts.googleapis.com/css2?family=Exo+2:wght@400;700&display=swap" rel="stylesheet">
<style>
  :root {
    --stage: #e9e7e3;
    --card-light: #f4f4f4;
    --card-mid: #e3e3e3;
    --green-dark: #3d8a2c;
    --green-light: #8cc24c;
    --swoosh-light: #d9d9d9;
    --swoosh-dark: #8e8e8e;
    --ink-white: #ffffff;
    --brand-ink: #5b5f63;
    --mark-fill: #d3d5d6;
  }
  html, body {
    margin: 0;
    width: 1200px;
    height: 768px;
    overflow: hidden;
    background: var(--stage);
  }
  .business-card {
    position: absolute;
    left: 120px;
    top: 108px;
    width: 960px;
    height: 552px;
    box-shadow: 0 18px 40px rgba(0,0,0,0.18);
    font-family: "Exo 2", sans-serif;
  }
  .card-art {
    position: absolute;
    inset: 0;
    display: block;
  }
  .brand-mark {
    position: absolute;
    left: 177px;
    top: 160px;
    width: 160px;
    height: 160px;
    border-radius: 50%;
    background: var(--mark-fill);
  }
  .brand-name {
    position: absolute;
    left: 74px;
    top: 336px;
    margin: 0;
    font-size: 46px;
    font-weight: 700;
    color: var(--brand-ink);
    white-space: nowrap;
  }
  .contact-panel {
    position: absolute;
    left: 640px;
    top: 0;
    color: var(--ink-white);
  }
  .person-name {
    position: absolute;
    top: 84px;
    margin: 0;
    font-size: 27px;
    font-weight: 400;
    letter-spacing: 0.5px;
    white-space: nowrap;
  }
  .person-role {
    position: absolute;
    top: 120px;
    margin: 0;
    font-size: 18px;
    white-space: nowrap;
  }
  .address {
    position: absolute;
    top: 240px;
    margin: 0;
    font-style: normal;
    font-size: 17px;
    line-height: 26px;
    white-space: nowrap;
  }
  .contact-list {
    position: absolute;
    top: 368px;
    margin: 0;
    padding: 0;
    list-style: none;
    font-size: 16px;
    line-height: 27.5px;
    white-space: nowrap;
  }
  .contact-list li {
    display: flex;
    align-items: center;
    gap: 8px;
  }
  .contact-icon {
    width: 14px;
    height: 14px;
    fill: var(--ink-white);
    flex: none;
  }
</style>
</head>
<body>
  <section class="business-card">
    <svg class="card-art" viewBox="0 0 960 552" width="960" height="552" aria-hidden="true">
      <defs>
        <linearGradient id="leftFace" x1="0" y1="0" x2="1" y2="1">
          <stop offset="0" stop-color="var(--card-light)"/>
          <stop offset="1" stop-color="var(--card-mid)"/>
        </linearGradient>
        <linearGradient id="greenFace" x1="0" y1="0" x2="1" y2="0">
          <stop offset="0" stop-color="var(--green-dark)"/>
          <stop offset="1" stop-color="var(--green-light)"/>
        </linearGradient>
        <linearGradient id="swoosh" x1="0" y1="0" x2="1" y2="0">
          <stop offset="0" stop-color="var(--swoosh-light)"/>
          <stop offset="1" stop-color="var(--swoosh-dark)"/>
        </linearGradient>
      </defs>
      <rect class="left-face" width="960" height="552" fill="url(#leftFace)"/>
      <path class="divider-swoosh" d="M492 0 C560 150 575 330 470 552 L540 552 C600 360 590 160 510 0 Z" fill="url(#swoosh)"/>
      <path class="green-face" d="M510 0 L960 0 L960 552 L528 552 C600 380 605 170 510 0 Z" fill="url(#greenFace)"/>
    </svg>

    <div class="brand-mark"></div>
    <p class="brand-name">Voranta Imports</p>

    <div class="contact-panel">
      <h1 class="person-name">Maren Ellery-Shaw</h1>
      <p class="person-role">consultant</p>
      <address class="address">214 9th floor,Arbor<br>Lane Road NHX</address>
      <ul class="contact-list">
        <li>
          <svg class="contact-icon" viewBox="0 0 16 16"><path d="M3.5 1 L6 1 L7 4.5 L5.3 5.8 C6.2 7.8 8.2 9.8 10.2 10.7 L11.5 9 L15 10 L15 12.5 C15 13.9 13.9 15 12.5 15 C6.7 15 1 9.3 1 3.5 C1 2.1 2.1 1 3.5 1 Z"/></svg>
          012 555 0147
        </li>
        <li>
          <svg class="contact-icon" viewBox="0 0 16 16"><path d="M4.5 0.5 H11.5 A1 1 0 0 1 12.5 1.5 V14.5 A1 1 0 0 1 11.5 15.5 H4.5 A1 1 0 0 1 3.5 14.5 V1.5 A1 1 0 0 1 4.5 0.5 Z M5 2.5 V12 H11 V2.5 Z M8 12.7 A0.9 0.9 0 1 0 8 14.5 A0.9 0.9 0 1 0 8 12.7 Z"/></svg>
          012 555 0148
        </li>
        <li>
          <svg class="contact-icon" viewBox="0 0 16 16"><path d="M4 1 H10 L12 3 V6 H4 Z M1.5 7 H14.5 V13 H12 V15 H4 V13 H1.5 Z M5 11 V14 H11 V11 Z"/></svg>
          012 555 0149
        </li>
        <li>
          <svg class="contact-icon" viewBox="0 0 16 16"><path d="M1 3 H15 V4 L8 9 L1 4 Z M1 5.5 L8 10.5 L15 5.5 V13 H1 Z"/></svg>
          maren@voranta.com
        </li>
        <li>
          <svg class="contact-icon" viewBox="0 0 16 16"><path d="M8 1 A7 7 0 1 0 8 15 A7 7 0 1 0 8 1 Z M8 2.4 A5.6 5.6 0 0 1 13.5 7.3 H2.5 A5.6 5.6 0 0 1 8 2.4 Z M2.5 8.7 H13.5 A5.6 5.6 0 0 1 2.5 8.7 Z" fill-rule="evenodd"/><path d="M7.3 1.5 H8.7 V14.5 H7.3 Z"/></svg>
          www.voranta-imports.com
        </li>
      </ul>
    </div>
  </section>
</body>
</html>
```